Revamp of our Premium Travel Website - BIG OPPORTUNITY -

This is our website's home page: www.velmorintrailways.com
We have already started a redesign, please see attached. Base on the content and info attached, please propose a new redesign which is much better and looks super premium.
We are looking for someone to hire to redesign 2 full websites.
Please change compass for logo attached. change logo as needed.
YOU HAVE THE FREEDOM TO CHANGE EVERYTHING TO MAKE IT LOOK PREMIUM AND GREAT!

Target Market(s)

United States

Number of Pages Required

1 page

Colors

Designer to choose colors to be used in the design.

Requirements
Must have
• Must look premium and unique.
• Must be responsive with mobile, tablet, and desktop.
Nice to have
• Color pallete that looks premium. It should include gold color. You can change completely the colors provided in the sample.
• Change all fonts, and logo as needed.

```html
<!DOCTYPE html>
<html lang="en">
<head>
<meta charset="utf-8">
<title>Velmorin Trailways – Home</title>
<link rel="stylesheet" href="https://fonts.googleapis.com/css2?family=Oswald:wght@400;500;600;700&family=Open+Sans:wght@400;600;700&display=swap">
<style>
:root{
  --gold:#d8891c;
  --gold-dark:#b8700f;
  --gold-soft:#e8b658;
  --ink:#1c1c1c;
  --ink-soft:#444;
  --cream:#f4ebd6;
  --footer:#0b0b0b;
  --line:#d5d5d5;
  --white:#fff;
}
*{box-sizing:border-box;margin:0;padding:0}
html,body{width:1200px;height:4500px;overflow:hidden}
body{font-family:"Open Sans",Arial,sans-serif;color:var(--ink);background:var(--white);position:relative}
.abs{position:absolute}
.head{font-family:"Oswald","Arial Narrow",sans-serif;text-transform:uppercase;font-weight:500}
.center{text-align:center;left:0;width:1200px}
.photo{overflow:hidden}

/* top bar */
.topbar{top:0;left:0;width:1200px;height:24px;background:#3a2a12;color:#f0d9a8;font-size:11px;display:flex;align-items:center;justify-content:space-between;padding:0 250px}
.topbar .dots{display:flex;gap:10px;align-items:center}
.topbar .dot{width:9px;height:9px;border-radius:50%;background:#f0d9a8}
.header{top:24px;left:0;width:1200px;height:84px;background:var(--white)}
.brand-name{left:360px;top:42px;font-size:16px;font-weight:700;font-family:"Oswald",sans-serif;letter-spacing:.5px}
.logo{left:240px;top:30px;width:110px;height:110px;border-radius:50%;background:var(--gold);border:5px solid var(--white);box-shadow:0 0 0 3px var(--gold-dark);z-index:5;display:flex;align-items:center;justify-content:center;text-align:center;color:var(--white);font-family:"Oswald",sans-serif;font-size:15px;font-weight:600;line-height:1.1}
.cta-top{left:790px;top:30px;width:170px;height:32px;border-radius:16px;background:var(--gold);color:var(--white);font-size:10px;font-weight:700;display:flex;align-items:center;justify-content:center}
.nav{top:108px;left:0;width:1200px;height:30px;background:var(--gold);display:flex;justify-content:flex-end;gap:26px;padding-right:235px;align-items:center;color:var(--white);font-size:11px;font-weight:700;font-family:"Oswald",sans-serif}

/* hero */
.hero{top:138px;left:0;width:1200px;height:552px;
  background:
    radial-gradient(ellipse 60% 30% at 50% 8%,rgba(230,236,240,.55),transparent 70%),
    radial-gradient(ellipse 35% 25% at 18% 30%,rgba(225,228,230,.45),transparent 70%),
    radial-gradient(ellipse 30% 22% at 82% 26%,rgba(215,220,224,.4),transparent 70%),
    radial-gradient(ellipse 70% 18% at 50% 88%,rgba(46,150,160,.75),transparent 75%),
    linear-gradient(180deg,#6f7c88 0%,#58585a 22%,#7a6f66 40%,#4f5148 55%,#2f4a36 70%,#2a6f74 86%,#16302e 100%)}
.hero-title{top:258px;font-size:38px;color:var(--white);font-weight:700;line-height:1.15;letter-spacing:1px;text-shadow:0 2px 8px rgba(0,0,0,.45)}
.promise{top:420px;width:170px;height:225px;background:var(--cream);text-align:center;padding:70px 12px 0;box-shadow:0 4px 12px rgba(0,0,0,.25)}
.promise .ico{position:absolute;top:-18px;left:55px;width:60px;height:60px;border-radius:50%;background:var(--gold-soft);border:3px solid var(--white)}
.promise h4{font-size:12px;font-weight:700;line-height:1.3;margin-bottom:10px}
.promise p{font-size:9px;color:var(--ink-soft);line-height:1.4;font-style:italic}
.promise .by{font-size:9px;font-weight:700;margin-top:12px;font-style:normal;color:var(--ink)}

/* dividers & titles */
.divider{width:160px;height:2px;background:linear-gradient(90deg,transparent,#888,transparent);left:520px}
.sec-title{font-size:26px;line-height:1.3;color:var(--ink)}
.sec-sub{font-size:13px;color:var(--ink-soft)}

/* form */
.field{top:804px;height:30px;border:1px solid var(--line);font-size:10px;color:#888;display:flex;align-items:center;padding-left:10px}
.go{top:804px;left:903px;width:45px;height:30px;background:var(--gold);color:var(--white);font-weight:700;font-size:11px;display:flex;align-items:center;justify-content:center}
.label{font-size:14px;font-weight:700}
.tile{width:160px;height:165px;display:flex;align-items:flex-end;justify-content:center;padding-bottom:22px;color:var(--white);font-size:13px;font-weight:600;text-shadow:0 1px 4px rgba(0,0,0,.6)}
.btn-gold{background:var(--gold);color:var(--white);font-family:"Oswald",sans-serif;font-weight:600;font-size:15px;border-radius:20px;display:flex;align-items:center;justify-content:center;text-transform:uppercase}

/* testimonial */
.guest-photo{left:0;top:1500px;width:591px;height:324px;
  background:
    radial-gradient(ellipse 28% 40% at 40% 55%,rgba(200,50,60,.55),transparent 70%),
    radial-gradient(ellipse 30% 45% at 22% 50%,rgba(40,90,180,.7),transparent 70%),
    radial-gradient(ellipse 25% 30% at 85% 75%,rgba(120,125,130,.8),transparent 70%),
    linear-gradient(100deg,#1f3f78 0%,#2c5ea0 35%,#7c8f9c 60%,#a9b6bc 78%,#4b5e46 100%)}
.guest{left:609px;top:1512px;width:360px}
.guest h3{font-family:"Oswald",sans-serif;font-weight:500;font-size:22px}
.guest .loc{font-size:14px;margin:4px 0 18px}
.guest p{font-size:10px;line-height:1.55;color:var(--ink-soft);margin-bottom:10px}
.guest .visited{font-weight:700;color:var(--ink);font-size:11px}
.pill{top:1854px;height:28px;border-radius:14px;font-size:11px;font-weight:700;display:flex;align-items:center;justify-content:center}
.pill.dark{background:var(--ink);color:var(--white)}
.pill.light{border:1.5px solid var(--gold);color:var(--ink)}
.review{left:355px;width:485px;height:28px;border-radius:14px;background:#ececec;font-size:11px;font-weight:600;display:flex;align-items:center;padding-left:18px;gap:20px}
.review .src{color:#555;font-size:11px;display:flex;align-items:center;gap:6px}
.review .sq{width:10px;height:10px;background:#777}

/* featured */
.feature{top:2142px;left:0;width:1200px;height:543px;
  background:
    radial-gradient(ellipse 14% 30% at 52% 70%,rgba(210,180,40,.85),transparent 70%),
    radial-gradient(ellipse 10% 16% at 52% 42%,rgba(60,40,30,.8),transparent 70%),
    radial-gradient(ellipse 20% 22% at 45% 95%,rgba(180,40,35,.7),transparent 70%),
    linear-gradient(180deg,#cfd6db 0%,#b9c3c8 12%,#eef1f2 20%,#9fb0ba 28%,#5f7a88 40%,#3e5a68 60%,#2a4452 80%,#1b2f3a 100%)}
.thumb{top:2580px;width:143px;height:99px}
.thumb.on{border:4px solid var(--gold)}
.city{left:245px;top:2708px;font-family:"Oswald",sans-serif;font-size:22px;font-weight:500}
.city-text{left:245px;top:2748px;width:710px;font-size:10px;line-height:1.55;color:var(--ink-soft)}
.read{left:245px;top:2822px;width:70px;height:22px;font-size:9px;border-radius:11px}
.other{top:2904px;width:240px;height:150px;display:flex;align-items:center;justify-content:center;color:var(--white);font-size:16px;font-weight:700;text-shadow:0 1px 5px rgba(0,0,0,.65)}
.other.on{border:4px solid var(--gold)}

/* itineraries */
.trip{top:3270px;width:190px}
.trip .pic{height:141px}
.trip h5{font-family:"Oswald",sans-serif;font-weight:400;font-size:13px;text-align:center;line-height:1.35;margin:12px 0 14px}
.trip .icons{display:flex;gap:6px;justify-content:center}
.trip .icons span{width:36px;height:36px;background:#e6e6e6;display:flex;align-items:center;justify-content:center}
.trip .btn-gold{width:160px;height:26px;margin:28px auto 0;font-size:11px}

/* contact band */
.band{top:3615px;left:0;width:1200px;height:495px;
  background:
    radial-gradient(ellipse 50% 30% at 30% 20%,rgba(95,90,82,.55),transparent 70%),
    radial-gradient(ellipse 45% 28% at 75% 15%,rgba(80,78,74,.5),transparent 70%),
    linear-gradient(180deg,#3a3632 0%,#26241f 40%,#1a1917 70%,#121212 100%)}
.band-title{top:3708px;color:var(--white);font-size:28px}
.band-orange{top:3770px;color:var(--gold);font-size:18px;line-height:1.35}
.band-text{top:3840px;color:#eee;font-size:15px;line-height:1.55}
.select{top:3984px;height:36px;border-bottom:1px solid #aaa;color:#ddd;font-size:12px;display:flex;align-items:center;justify-content:space-between;padding:0 10px}
.search{top:3980px;left:800px;width:155px;height:42px;font-size:18px;border-radius:21px}

/* footer */
.footer{top:4110px;left:0;width:1200px;height:300px;background:var(--footer)}
.fcol{top:4170px;color:#ddd;font-size:11px}
.fcol h6{color:var(--gold);font-size:14px;font-weight:600;margin-bottom:12px}
.fcol li{list-style:none;margin-bottom:9px;padding-left:14px;position:relative}
.fcol li:before{content:"";position:absolute;left:0;top:4px;width:5px;height:5px;background:var(--gold)}
.flogo{left:810px;top:4155px;width:150px;height:150px;border-radius:50%;background:var(--gold);border:6px solid #f2d48e;display:flex;align-items:center;justify-content:center;text-align:center;color:var(--white);font-family:"Oswald",sans-serif;font-size:20px;font-weight:600;line-height:1.1}
.help{left:835px;top:4322px;color:var(--gold);font-weight:700;font-size:15px}
.fphone{left:822px;top:4348px;color:var(--white);font-weight:700;font-size:18px}
.bottom{top:4410px;left:0;width:1200px;height:90px;background:#000}
.badge{left:490px;top:4435px;width:100px;height:40px;background:#ddd}
.lang{left:790px;top:4442px;width:165px;height:26px;background:var(--white);color:#333;font-size:10px;display:flex;align-items:center;padding-left:8px}
</style>
</head>
<body>

<div class="abs topbar"><span>OUR GUESTS ARE TALKING ABOUT US</span>
  <span class="dots"><i class="dot"></i><i class="dot"></i><i class="dot"></i>
  <svg width="10" height="10" viewBox="0 0 24 24"><path fill="#f0d9a8" d="M6.6 10.8a15 15 0 0 0 6.6 6.6l2.2-2.2a1 1 0 0 1 1-.25 11.4 11.4 0 0 0 3.6.57 1 1 0 0 1 1 1V20a1 1 0 0 1-1 1A17 17 0 0 1 3 4a1 1 0 0 1 1-1h3.5a1 1 0 0 1 1 1c0 1.25.2 2.45.57 3.6a1 1 0 0 1-.25 1z"/></svg>
  <span>1-888 555 0142</span></span>
</div>

<header class="abs header">
  <div class="abs brand-name">VELMORIN TRAILWAYS</div>
  <div class="abs cta-top">GET YOUR CUSTOM ITINERARY</div>
</header>
<div class="abs logo">VELMORIN<br>TRAILWAYS</div>
<nav class="abs nav"><span>HOME</span><span>ABOUT US</span><span>SAMPLE ITINERARIES</span><span>TESTIMONIALS</span></nav>

<section class="abs hero photo" role="img" aria-label="Snowy mountain range above a forest and turquoise glacier lake"></section>
<h1 class="abs center head hero-title">Bring back home the sweetest collection<br>of ever-lasting memories</h1>

<div class="abs promise" style="left:245px"><span class="ico"></span><h4>Experience the peace of mind of a worry-free tour</h4><p>"Every detail was handled so we could simply enjoy the trip."</p><p class="by">— Nora Pell &amp; Family</p></div>
<div class="abs promise" style="left:425px"><span class="ico"></span><h4>Unparalleled personalized care 24/7</h4><p>"Our team answered every question, day or night, with care."</p><p class="by">— Owen &amp; Lia Marsh</p></div>
<div class="abs promise" style="left:605px"><span class="ico"></span><h4>Hand picked tour guides to guarantee a first-class experience</h4><p>"Our guides were warm, sharp and truly local experts."</p><p class="by">— Tom &amp; Ada Riker</p></div>
<div class="abs promise" style="left:785px"><span class="ico"></span><h4>Impressive Trip Reviews From Guests who You Can Contact!</h4><p>"Ask any past guest; the best travel agency we have worked with."</p><p class="by">— Hugh Brandt</p></div>

<div class="abs divider" style="top:696px"></div>
<h2 class="abs center head sec-title" style="top:712px">Get a custom itinerary in under 24 hours, and benefit from<br>our travel experts' invaluable advice</h2>

<div class="abs field" style="left:255px;width:150px">Trip Start Date</div>
<div class="abs field" style="left:415px;width:150px">Trip Duration</div>
<div class="abs field" style="left:575px;width:150px">Number of Rooms</div>
<div class="abs field" style="left:735px;width:160px">Looking For?</div>
<div class="abs go">GO</div>

<div class="abs label" style="left:255px;top:852px">Pick Your Destination</div>
<div class="abs tile" style="left:255px;top:885px;background:radial-gradient(ellipse 40% 45% at 50% 45%,rgba(140,110,80,.7),transparent 70%),linear-gradient(180deg,#8a8d90,#55585b 50%,#2a2c2e)" role="img" aria-label="Traveller with backpack">Suggest for me</div>
<div class="abs tile" style="left:430px;top:885px;background:radial-gradient(ellipse 35% 35% at 50% 35%,rgba(235,235,230,.8),transparent 70%),linear-gradient(180deg,#7aa0c8,#a9b9c8 45%,#5c5f62 75%,#3a3a3a)" role="img" aria-label="Domed building in Buenos Aires">Buenos Aires</div>
<div class="abs tile" style="left:605px;top:885px;background:radial-gradient(ellipse 40% 40% at 50% 30%,rgba(240,240,240,.85),transparent 70%),linear-gradient(180deg,#d3d7da,#8e979a 50%,#3a4640)" role="img" aria-label="Person at a waterfall viewpoint">Iguazu Falls</div>
<div class="abs tile" style="left:780px;top:885px;background:radial-gradient(ellipse 50% 30% at 50% 30%,rgba(200,190,180,.6),transparent 70%),linear-gradient(180deg,#a7a49f,#6f6a62 45%,#33302b)" role="img" aria-label="Winding mountain road in Mendoza">Mendoza</div>
<div class="abs tile" style="left:255px;top:1074px;background:radial-gradient(ellipse 60% 25% at 50% 70%,rgba(200,215,225,.8),transparent 70%),linear-gradient(180deg,#7fa6c4,#9fb4c0 45%,#556066 75%,#2e3b3e)" role="img" aria-label="Hikers above a glacier">El Calafate</div>
<div class="abs tile" style="left:430px;top:1074px;background:radial-gradient(ellipse 50% 25% at 50% 60%,rgba(90,120,150,.7),transparent 70%),linear-gradient(180deg,#b9c6d0,#8f9ba3 40%,#5d5a4c 75%,#3d3a30)" role="img" aria-label="Lakeside town of Bariloche">Bariloche</div>
<div class="abs tile" style="left:605px;top:1074px;background:radial-gradient(ellipse 50% 30% at 50% 40%,rgba(240,180,90,.8),transparent 70%),linear-gradient(180deg,#e0a660,#b8763e 45%,#6a4630 75%,#3e2a1f)" role="img" aria-label="Ushuaia at sunset">Ushuaia</div>
<div class="abs tile" style="left:780px;top:1074px;background:radial-gradient(ellipse 60% 20% at 50% 55%,rgba(60,140,190,.8),transparent 70%),linear-gradient(180deg,#4a7fb5,#3f77a8 45%,#5c7046 75%,#3b4a2b)" role="img" aria-label="Peninsula coastline">Peninsula Valdes</div>

<div class="abs btn-gold" style="left:411px;top:1284px;width:384px;height:32px">Get your custom itinerary in 24 hours</div>

<div class="abs divider" style="top:1356px"></div>
<h2 class="abs center head sec-title" style="top:1374px">Our guests are raving about us!</h2>
<p class="abs center sec-sub" style="top:1420px">Read the True Reviews of our Past Guests! (and contact any of them if you'd like)</p>

<div class="abs guest-photo photo" role="img" aria-label="Family sitting in the open back of a car on a road trip"></div>
<div class="abs guest">
  <h3>Daniel &amp; Ruth Halloway and Family</h3>
  <div class="loc">(Chapel Hill, North Carolina, United States)</div>
  <p>"It seemed impossible. Three generations, seven people, ten days, four locations, domestic travel, tours, transfers, and accommodations. All worry-free and better made."</p>
  <p>"So what happened? Everything was on time, as described, with outstanding people, and the team was always a step ahead of us."</p>
  <p>"I have never had an experience like this one and would recommend it to anyone."</p>
  <p class="visited">Daniel &amp; Ruth visited: Buenos Aires, Bariloche, El Calafate and Ushuaia.</p>
</div>

<div class="abs pill light" style="left:245px;width:165px">See Full Testimonials</div>
<div class="abs pill dark" style="left:425px;width:165px">See Booked Itinerary</div>
<div class="abs pill dark" style="left:605px;width:165px">Contact This Guest</div>
<div class="abs pill dark" style="left:785px;width:170px">Get Your Custom Itinerary</div>

<div class="abs review" style="top:1922px"><span class="src"><i class="sq"></i>TrekReview</span>Read trip reviews our guests have posted on TrekReview</div>
<div class="abs review" style="top:1972px"><span class="src"><i class="sq"></i>SocialPage</span>Read trip reviews our guests have posted on SocialPage</div>

<div class="abs divider" style="top:2040px"></div>
<h2 class="abs center head sec-title" style="top:2056px">Featured destination: Patagonia region</h2>
<p class="abs center" style="top:2100px;font-size:15px">(The Last Refuge of Nature)</p>

<div class="abs feature photo" role="img" aria-label="Kayaker in a yellow vest paddling toward a glacier wall"></div>
<div class="abs thumb on" style="left:245px;background:radial-gradient(ellipse 30% 40% at 50% 60%,rgba(220,180,40,.8),transparent 70%),linear-gradient(180deg,#8fa8b8,#3b6f9a 50%,#b3412e)" role="img" aria-label="Kayak on the water"></div>
<div class="abs thumb" style="left:388px;background:radial-gradient(ellipse 40% 30% at 50% 45%,rgba(240,240,245,.8),transparent 70%),linear-gradient(180deg,#4a76b2,#8ba1b0 60%,#6a5a48)" role="img" aria-label="Snowy mountain peaks"></div>
<div class="abs thumb" style="left:531px;background:radial-gradient(ellipse 40% 35% at 50% 60%,rgba(90,70,55,.8),transparent 70%),linear-gradient(180deg,#9aa3a8,#6a7075 50%,#3a3a38)" role="img" aria-label="Coastal wildlife"></div>
<div class="abs thumb" style="left:674px;background:radial-gradient(ellipse 45% 30% at 50% 50%,rgba(225,232,238,.85),transparent 70%),linear-gradient(180deg,#a9b8c6,#7f919c 55%,#5b6a62)" role="img" aria-label="Glacier"></div>
<div class="abs thumb" style="left:817px;background:radial-gradient(ellipse 20% 40% at 50% 55%,rgba(190,60,50,.75),transparent 70%),linear-gradient(180deg,#e6ad62,#c07b3e 55%,#5d4230)" role="img" aria-label="Lighthouse at dusk"></div>
<div class="abs thumb" style="left:960px;background:radial-gradient(ellipse 50% 25% at 50% 70%,rgba(70,130,200,.8),transparent 70%),linear-gradient(180deg,#7fa2cc,#5f87ba 50%,#2b3f5c)" role="img" aria-label="Blue lake"></div>

<h3 class="abs city">Buenos Aires (City of Tango)</h3>
<p class="abs city-text">It's the birthplace and capital of tango, and much like the dance itself, Buenos Aires is a sensual and captivating city with an eclectic, original and distinguished collection of architecture, delectable food, vibrant culture, and a plenty of fascinating cultural highlights to enjoy. It's home to some of the most important museums of Latin American art, and the best tango musicians, dancers, and singers worldwide, all of whom you can see perform in the city's top tango venues...</p>
<div class="abs btn-gold read">Read More</div>

<div class="abs label" style="left:245px;top:2862px;font-family:'Oswald',sans-serif;font-size:18px;font-weight:500">See Our Other Suggested Destinations</div>
<div class="abs other" style="left:0;background:radial-gradient(ellipse 40% 30% at 40% 65%,rgba(150,90,60,.6),transparent 70%),linear-gradient(180deg,#9aaab5,#6c7f8d 45%,#2c3a3f)" role="img" aria-label="Ushuaia harbour with boats">Ushuaia</div>
<div class="abs other on" style="left:240px;background:radial-gradient(ellipse 40% 40% at 50% 40%,rgba(220,225,215,.6),transparent 70%),linear-gradient(180deg,#8a9a84,#5e6e50 50%,#3b4a32)" role="img" aria-label="Iguazu waterfalls">Iguazu Falls</div>
<div class="abs other" style="left:480px;background:radial-gradient(ellipse 55% 30% at 50% 65%,rgba(235,240,245,.9),transparent 70%),linear-gradient(180deg,#4f86c6,#8fb0d4 45%,#dfe6ec 75%,#6d8aa6)" role="img" aria-label="Glacier front">El Calafate</div>
<div class="abs other" style="left:720px;background:radial-gradient(ellipse 30% 40% at 30% 50%,rgba(200,70,60,.6),transparent 70%),radial-gradient(ellipse 30% 40% at 75% 45%,rgba(70,130,180,.5),transparent 70%),linear-gradient(180deg,#e0a866,#b87848 50%,#6b4a36)" role="img" aria-label="Colourful street scene in Buenos Aires"></div>
<div class="abs other" style="left:960px;background:radial-gradient(ellipse 50% 25% at 50% 40%,rgba(210,205,195,.6),transparent 70%),linear-gradient(180deg,#a6b2b8,#8a8576 50%,#4d4233)" role="img" aria-label="Vineyard road in Mendoza">Mendoza</div>

<div class="abs divider" style="top:3105px"></div>
<h2 class="abs center head sec-title" style="top:3124px">Check out our sample travel itineraries</h2>
<p class="abs center" style="top:3166px;font-size:15px;line-height:1.45;color:var(--ink-soft)">If you are Looking for a First-class Argentina Travel Experience see our Suggested Argentina<br>Travel Packages Below!</p>

<div class="abs trip" style="left:245px"><div class="pic" style="background:radial-gradient(ellipse 40% 40% at 60% 50%,rgba(70,100,140,.6),transparent 70%),linear-gradient(180deg,#a0ad8c,#7b8a6b 45%,#4b4a3a)" role="img" aria-label="Travellers at a scenic viewpoint"></div><h5>An Exclusive Adventure at the Scenic Patagonia Region and the Mighty Iguazu Falls</h5><div class="icons"><span><svg width="16" height="16" viewBox="0 0 24 24"><rect x="3" y="5" width="18" height="16" fill="none" stroke="#999" stroke-width="2"/><path d="M3 10h18" stroke="#999" stroke-width="2"/></svg></span><span><svg width="16" height="16" viewBox="0 0 24 24"><path d="M12 2a7 7 0 0 0-7 7c0 5 7 13 7 13s7-8 7-13a7 7 0 0 0-7-7z" fill="none" stroke="#999" stroke-width="2"/><circle cx="12" cy="9" r="2.5" fill="#999"/></svg></span><span><svg width="16" height="16" viewBox="0 0 24 24"><rect x="3" y="5" width="18" height="14" fill="none" stroke="#999" stroke-width="2"/><path d="M5 17l5-6 4 4 2-2 3 4" fill="none" stroke="#999" stroke-width="2"/></svg></span></div><div class="btn-gold">See Itinerary Details</div></div>
<div class="abs trip" style="left:485px"><div class="pic" style="background:radial-gradient(ellipse 45% 35% at 50% 60%,rgba(230,170,60,.85),transparent 70%),linear-gradient(180deg,#4f7fbf,#7a9ccc 40%,#c38a3e 75%,#6a4a2a)" role="img" aria-label="Ornate temple roofs"></div><h5>An Exclusive Adventure at the Scenic Patagonia Region and the Mighty Iguazu Falls</h5><div class="icons"><span><svg width="16" height="16" viewBox="0 0 24 24"><rect x="3" y="5" width="18" height="16" fill="none" stroke="#999" stroke-width="2"/><path d="M3 10h18" stroke="#999" stroke-width="2"/></svg></span><span><svg width="16" height="16" viewBox="0 0 24 24"><path d="M12 2a7 7 0 0 0-7 7c0 5 7 13 7 13s7-8 7-13a7 7 0 0 0-7-7z" fill="none" stroke="#999" stroke-width="2"/><circle cx="12" cy="9" r="2.5" fill="#999"/></svg></span><span><svg width="16" height="16" viewBox="0 0 24 24"><rect x="3" y="5" width="18" height="14" fill="none" stroke="#999" stroke-width="2"/><path d="M5 17l5-6 4 4 2-2 3 4" fill="none" stroke="#999" stroke-width="2"/></svg></span></div><div class="btn-gold">See Itinerary Details</div></div>
<div class="abs trip" style="left:725px"><div class="pic" style="background:radial-gradient(ellipse 40% 35% at 50% 55%,rgba(90,60,40,.75),transparent 70%),linear-gradient(180deg,#b9c1c6,#9aa3a8 40%,#7a6a52 70%,#5a4532)" role="img" aria-label="Horse riders in the countryside"></div><h5>An Exclusive Adventure at the Scenic Patagonia Region and the Mighty Iguazu Falls</h5><div class="icons"><span><svg width="16" height="16" viewBox="0 0 24 24"><rect x="3" y="5" width="18" height="16" fill="none" stroke="#999" stroke-width="2"/><path d="M3 10h18" stroke="#999" stroke-width="2"/></svg></span><span><svg width="16" height="16" viewBox="0 0 24 24"><path d="M12 2a7 7 0 0 0-7 7c0 5 7 13 7 13s7-8 7-13a7 7 0 0 0-7-7z" fill="none" stroke="#999" stroke-width="2"/><circle cx="12" cy="9" r="2.5" fill="#999"/></svg></span><span><svg width="16" height="16" viewBox="0 0 24 24"><rect x="3" y="5" width="18" height="14" fill="none" stroke="#999" stroke-width="2"/><path d="M5 17l5-6 4 4 2-2 3 4" fill="none" stroke="#999" stroke-width="2"/></svg></span></div><div class="btn-gold">See Itinerary Details</div></div>

<section class="abs band photo" role="img" aria-label="Dark mountain landscape backdrop"></section>
<h2 class="abs center head band-title">Contact any of 130+ past guests from the United States</h2>
<p class="abs center band-orange">No other company will offer you a list of over one hundred guests who you can<br>choose from to contact directly</p>
<p class="abs center band-text">Our guests have had superb travel experiences; contact them and check out firsthand what they<br>have to say about our Worry-Free &amp; First-Class tour experiences!</p>
<p class="abs center" style="top:3900px;color:#eee;font-size:15px">Select the type of guests you're interested Destinations Visited by the Guest in contacting</p>
<div class="abs select" style="left:255px;width:250px">Select Type <span>▾</span></div>
<div class="abs select" style="left:525px;width:250px">Select Destination <span>▾</span></div>
<div class="abs btn-gold search">Search</div>

<footer class="abs footer"></footer>
<div class="abs fcol" style="left:245px"><h6>Vacation Type</h6><ul><li>Argentina Honeymoon</li><li>Argentina Family Vacation</li><li>Customized Trips to Argentina</li><li>Argentina Travel Packages</li></ul></div>
<div class="abs fcol" style="left:447px"><h6>Destinations</h6><ul><li>Iguazu Falls Package</li><li>El Calafate Package</li><li>Buenos Aires Package</li><li>Bariloche Package</li><li>Ushuaia Package</li><li>Mendoza Package</li><li>Peninsula Valdes Package</li><li>Patagonia Package</li></ul></div>
<div class="abs fcol" style="left:630px"><h6>Velmorin Trailways</h6><ul><li>About Us</li><li>Contact Us</li><li>Site Map</li><li>Privacy Policy</li><li>Terms &amp; Conditions</li></ul></div>
<div class="abs flogo">VELMORIN<br>TRAILWAYS</div>
<div class="abs help"><svg width="13" height="13" viewBox="0 0 24 24" style="vertical-align:-1px"><path fill="#d8891c" d="M6.6 10.8a15 15 0 0 0 6.6 6.6l2.2-2.2a1 1 0 0 1 1-.25 11.4 11.4 0 0 0 3.6.57 1 1 0 0 1 1 1V20a1 1 0 0 1-1 1A17 17 0 0 1 3 4a1 1 0 0 1 1-1h3.5a1 1 0 0 1 1 1c0 1.25.2 2.45.57 3.6a1 1 0 0 1-.25 1z"/></svg> Need Help</div>
<div class="abs fphone">1-888 555 0142</div>

<div class="abs bottom"></div>
<div class="abs" style="left:245px;top:4448px;color:#aaa;font-size:10px">© 2019 | www.velmorintrailways.com</div>
<div class="abs badge"></div>
<div class="abs" style="left:600px;top:4437px;width:170px;color:#aaa;font-size:8px;line-height:1.35">Velmorin Trailways is officially licensed by the national Ministry of Tourism. Tour Operator License Number 12345.</div>
<div class="abs lang">Select Language ▾</div>

</body>
</html>
```